Panty packaging

what we are looking for is 1 of a kind packaging for women's panties. It should have the same theme for all styles but a different outline or a color code setting the difference between styles. Most company's are packaging in a poly bag or hanger, what we are looking for is a box packaging. also customer should be able to see whats in the box without having to open the box. If there are different colors, the window should show that. We want to be able to customize the design for different styles and for 1 color package or multi color package. It should be sleek and sophisticated. Box does not have to be square, it can have curved edges or be totally round, the most important thins is that it should be stack-able. Sometimes the box will hold a pack of 3 and sometimes a single item, so box height may vary. We need a graphic on the box to indicate the style, for example: hipster, brief, hi cut, or lo cut. box needs a space to put a small size chart. Out logo can be color changed to match theme and background colors, just stick with the 3 colors, black, white, and magneta.
Female market all ages. upscale market
It Company

```html
<!DOCTYPE html>
<html lang="en">
<head>
<meta charset="utf-8">
<title>Velmora Elegant Panties – Box Range</title>
<link href="https://fonts.googleapis.com/css2?family=Source+Sans+3:wght@300;400;600;700&display=swap" rel="stylesheet">
<style>
  :root{
    --stage:#5a5a5a;
    --magenta:#e0117f;
    --magenta-dark:#b80c67;
    --black:#141414;
    --black-lid:#262626;
    --white:#f6f6f6;
    --white-lid:#ffffff;
    --grey:#c4c4c4;
    --grey-dark:#9a9a9a;
    --beige:#d9c3a5;
    --beige-dark:#b89c78;
    --cream:#efe3cf;
    --ink:#3a3a3a;
    --lace-a:#c7a686;
    --lace-b:#f1e7dc;
  }
  *{box-sizing:border-box;margin:0;padding:0}
  html,body{width:1200px;height:1000px;overflow:hidden}
  body{background:var(--stage);font-family:"Source Sans 3",sans-serif;position:relative}

  .box{position:absolute}
  .box-lid{position:absolute;left:0;right:0;top:0;height:50px;border-radius:8px 8px 2px 2px}
  .box-body{position:absolute;left:6px;right:6px;top:50px;bottom:0;border-radius:0 0 6px 6px}
  .box--magenta .box-lid{background:var(--magenta)}
  .box--magenta .box-body{background:var(--magenta-dark)}
  .box--black .box-lid{background:var(--black-lid)}
  .box--black .box-body{background:var(--black)}
  .box--white .box-lid{background:var(--white-lid)}
  .box--white .box-body{background:var(--white)}

  .window{position:absolute;left:26px;top:84px;width:36px;border:2px solid #d8d0c4;
    background:linear-gradient(160deg,var(--lace-b),var(--lace-a) 45%,var(--lace-b) 70%,var(--lace-a))}

  .label{position:absolute;left:50%;transform:translateX(-50%);width:150px;height:150px;
    display:flex;align-items:center;justify-content:center}
  .label-frame{position:absolute;inset:0}
  .label-frame--scallop{border-radius:44%}
  .label-frame--bracket{border-radius:28px 28px 50% 50% / 28px 28px 22px 22px}
  .label-oval{position:relative;width:104px;height:96px;border-radius:50%;
    display:flex;flex-direction:column;align-items:center;justify-content:center;text-align:center}
  .brand{font-weight:300;font-size:21px;letter-spacing:.5px;color:var(--ink);line-height:1}
  .tagline{font-size:9px;color:var(--ink);margin-top:2px}
  .style-pill{margin-top:7px;padding:2px 12px;border-radius:50%;font-size:13px;font-weight:600;color:#fff}

  .bow{position:absolute;left:50%;transform:translateX(-50%);width:50px;height:24px;border-radius:6px;background:#2b2b2b}

  .size-tag{position:absolute;width:30px;height:30px;border-radius:50%;background:var(--beige);
    font-size:10px;font-weight:700;color:var(--ink);display:flex;align-items:center;justify-content:center}
  .pin{position:absolute;width:2px;height:68px;background:#9c9c9c;transform:rotate(-32deg);transform-origin:top}
  .pin-head{position:absolute;width:7px;height:14px;border-radius:50%;background:var(--magenta)}
</style>
</head>
<body>

<!-- Top row -->
<section class="box box--magenta" style="left:100px;top:262px;width:300px;height:290px">
  <div class="box-lid"></div><div class="box-body"></div>
  <div class="window" style="height:180px" role="img" aria-label="Window showing white lace panties"></div>
  <div class="label" style="top:92px">
    <div class="label-frame label-frame--scallop" style="background:var(--grey)" role="img" aria-label="Grey polka-dot scalloped label frame"></div>
    <div class="label-oval" style="background:#fff">
      <span class="brand">Velmora</span><span class="tagline">Elegant Panties</span>
      <span class="style-pill" style="background:var(--grey-dark);color:var(--magenta)">hipster</span>
    </div>
  </div>
  <div class="bow" style="top:80px" role="img" aria-label="Black satin bow"></div>
  <div class="pin-head" style="left:236px;top:68px"></div><div class="pin" style="left:242px;top:80px"></div>
  <div class="size-tag" style="left:246px;top:84px">size</div>
</section>

<section class="box box--black" style="left:455px;top:262px;width:295px;height:290px">
  <div class="box-lid"></div><div class="box-body"></div>
  <div class="window" style="height:180px" role="img" aria-label="Window showing white lace panties"></div>
  <div class="label" style="top:92px">
    <div class="label-frame label-frame--bracket" style="background:var(--magenta)"></div>
    <div class="label-frame label-frame--bracket" style="inset:5px;background:var(--grey)"></div>
    <div class="label-oval">
      <span class="brand">Velmora</span><span class="tagline">Elegant Panties</span>
      <span class="style-pill" style="background:var(--grey-dark)">lo cut</span>
    </div>
  </div>
  <div class="bow" style="top:80px" role="img" aria-label="Black satin bow"></div>
  <div class="pin-head" style="left:232px;top:68px"></div><div class="pin" style="left:238px;top:80px"></div>
  <div class="size-tag" style="left:226px;top:96px">size</div>
</section>

<section class="box box--white" style="left:840px;top:262px;width:300px;height:290px">
  <div class="box-lid"></div><div class="box-body"></div>
  <div class="window" style="height:180px" role="img" aria-label="Window showing white lace panties"></div>
  <div class="label" style="top:100px">
    <div class="label-frame label-frame--scallop" style="background:var(--magenta)" role="img" aria-label="Magenta polka-dot scalloped label frame"></div>
    <div class="label-frame label-frame--scallop" style="inset:8px;background:var(--beige)"></div>
    <div class="label-oval" style="background:var(--beige)">
      <span class="brand">Velmora</span><span class="tagline">Elegant Panties</span>
      <span class="style-pill" style="background:var(--beige-dark)">brief</span>
    </div>
  </div>
  <div class="bow" style="top:88px;left:190px" role="img" aria-label="Black satin bow"></div>
  <div class="pin-head" style="left:242px;top:74px"></div><div class="pin" style="left:248px;top:86px"></div>
  <div class="size-tag" style="left:240px;top:118px">size</div>
</section>

<!-- Bottom row -->
<section class="box box--black" style="left:180px;top:566px;width:285px;height:236px">
  <div class="box-lid"></div><div class="box-body"></div>
  <div class="window" style="left:24px;top:70px;height:150px" role="img" aria-label="Window showing white lace panties"></div>
  <div class="label" style="top:72px">
    <div class="label-frame label-frame--scallop" style="background:var(--magenta)" role="img" aria-label="Magenta and grey striped scalloped label frame"></div>
    <div class="label-oval" style="background:#fff">
      <span class="brand">Velmora</span><span class="tagline">Elegant Panties</span>
      <span class="style-pill" style="background:var(--grey);color:var(--ink)">lo cut</span>
    </div>
  </div>
  <div class="bow" style="top:60px" role="img" aria-label="Black satin bow"></div>
  <div class="pin-head" style="left:234px;top:58px"></div><div class="pin" style="left:240px;top:70px"></div>
  <div class="size-tag" style="left:222px;top:84px">size</div>
</section>

<section class="box box--black" style="left:470px;top:566px;width:285px;height:236px">
  <div class="box-lid"></div><div class="box-body"></div>
  <div class="window" style="left:24px;top:70px;height:150px" role="img" aria-label="Window showing white lace panties"></div>
  <div class="label" style="top:72px;width:130px">
    <div class="label-frame label-frame--bracket" style="background:var(--grey)" role="img" aria-label="Grey and beige striped label frame"></div>
    <div class="label-oval" style="width:92px;background:var(--cream)">
      <span class="brand" style="font-size:18px">Velmora</span><span class="tagline">Elegant Panties</span>
      <span class="style-pill" style="background:var(--beige-dark)">hi cut</span>
    </div>
  </div>
  <div class="bow" style="top:60px" role="img" aria-label="Black satin bow"></div>
  <div class="pin-head" style="left:230px;top:58px"></div><div class="pin" style="left:236px;top:70px"></div>
  <div class="size-tag" style="left:198px;top:84px">size</div>
</section>

<section class="box box--black" style="left:760px;top:566px;width:285px;height:236px">
  <div class="box-lid"></div><div class="box-body"></div>
  <div class="window" style="left:24px;top:70px;height:150px" role="img" aria-label="Window showing white lace panties"></div>
  <div class="label" style="top:72px;width:130px">
    <div class="label-frame label-frame--bracket" style="background:var(--magenta)"></div>
    <div class="label-frame label-frame--bracket" style="inset:5px;background:var(--beige)"></div>
    <div class="label-oval" style="width:100px">
      <span class="brand" style="font-size:19px">Velmora</span><span class="tagline">Elegant Panties</span>
      <span class="style-pill" style="background:var(--beige-dark)">hi cut</span>
    </div>
  </div>
  <div class="bow" style="top:60px" role="img" aria-label="Black satin bow"></div>
  <div class="pin-head" style="left:232px;top:56px"></div><div class="pin" style="left:238px;top:68px"></div>
  <div class="size-tag" style="left:212px;top:70px">size</div>
</section>

</body>
</html>
```